Lunelle Rosa Hair Fancy Business Card’s

I want my business cards to be elite, original and very classy. I want the business cards to match the colors of my logo and to match the design posted. I would love the design of the picture I posted

I want the card all white .
The dripping on the top of the card I want it to match the pink color in my logo that’s also posted .
I need my logo on the business card !
I need my Instagram- @lunelle.rosa.hair__
And my phone number - 555 207 3962

Target Market(s)

My target market is young woman age 23 to older woman to the age of 65
I want both older and younger women to love my design . I don’t want any cheap looking business cards

Industry/Entity Type

Hair And Beauty

Contact Information for Business Card

Add my logo
Add my Instagram- @lunelle.rosa.hair__
My number - 555 207 3962
My website- www.lunellerosahair.example

Font styles to use
Serif
Script

Colors
ffffff
e667a6
e34298

Requirements
Must have
• The business cards must have my logo, my number , my website, and my Instagram!
Nice to have
• Nice to have glitter words that match my logo
• The business cards must look classy and mature
• I want them to be very unique!!
Should not have
• Should not have any colors that doesn’t match my logo ! This is very important! Please

```html
<!DOCTYPE html>
<html lang="en">
<head>
<meta charset="utf-8">
<title>Lunelle Rosa Hair – Business Card</title>
<link rel="stylesheet" href="https://fonts.googleapis.com/css2?family=Great+Vibes&family=Cinzel:wght@600&family=Poppins:wght@400&display=swap">
<style>
  :root {
    --backdrop: #161616;
    --card-white: #ffffff;
    --frame-pink: #c46aa9;
    --frame-pink-deep: #a9508f;
    --brand-pink: #e34298;
    --brand-pink-soft: #e667a6;
    --title-grey: #707070;
    --text-grey: #4a4a4a;
    --back-slate: #3f3f47;
  }
  * { margin: 0; padding: 0; box-sizing: border-box; }
  html, body { width: 1125px; height: 1200px; overflow: hidden; background: var(--backdrop); }
  .canvas { position: relative; width: 1125px; height: 1200px; background: var(--backdrop); }

  .card { position: absolute; left: 157px; width: 825px; height: 472px; }

  .card-front {
    top: 106px;
    padding: 13px 14px;
    background: linear-gradient(135deg, var(--frame-pink), var(--frame-pink-deep) 50%, var(--frame-pink));
  }
  .card-front .face { position: relative; width: 100%; height: 100%; background: var(--card-white); overflow: hidden; }

  .holder-name {
    position: absolute; left: 42px; top: 28px;
    font-family: "Great Vibes", cursive;
    font-size: 56px; line-height: 1; color: var(--brand-pink);
    white-space: nowrap;
  }
  .holder-title {
    position: absolute; left: 42px; top: 86px;
    font-family: "Cinzel", serif; font-weight: 600;
    font-size: 24px; line-height: 1.2; letter-spacing: 1px; color: var(--title-grey);
  }

  .contact-list {
    position: absolute; right: 40px; top: 284px;
    list-style: none;
    font-family: "Poppins", sans-serif; font-size: 19px; color: var(--text-grey);
  }
  .contact-list li { display: flex; align-items: center; height: 34.5px; white-space: nowrap; }
  .contact-list svg { width: 22px; height: 22px; margin-right: 12px; flex: none; }

  .card-back { top: 639px; background: var(--back-slate); display: flex; align-items: center; justify-content: center; }
  .brand-name {
    font-family: "Poppins", sans-serif; font-weight: 400;
    font-size: 50px; letter-spacing: 2px; color: var(--brand-pink);
  }
</style>
</head>
<body>
<main class="canvas">
  <section class="card card-front" aria-label="Business card front">
    <div class="face">
      <p class="holder-name">Daniel Hart</p>
      <p class="holder-title">PRESIDENT</p>
      <ul class="contact-list">
        <li>
          <svg viewBox="0 0 22 22" aria-hidden="true"><circle cx="11" cy="11" r="9.5" fill="none" stroke="var(--brand-pink)" stroke-width="2"/><path d="M7.5 6.5c-.8.8-.6 2.7 1.6 5.2s4.3 3.4 5.3 2.5l1-1-2-1.8-1 .8c-.8-.3-2.2-1.7-2.6-2.6l.8-1-1.8-2z" fill="var(--brand-pink)"/></svg>
          <span>555 207 3962</span>
        </li>
        <li>
          <svg viewBox="0 0 22 22" aria-hidden="true"><circle cx="11" cy="11" r="9.5" fill="none" stroke="var(--brand-pink)" stroke-width="2"/></svg>
          <span>@lunelle.rosa.hair__</span>
        </li>
        <li>
          <svg viewBox="0 0 22 22" aria-hidden="true"><circle cx="11" cy="11" r="9.5" fill="none" stroke="var(--brand-pink)" stroke-width="2"/><rect x="6.5" y="8" width="9" height="6.5" fill="var(--brand-pink)"/><path d="M6.5 8l4.5 3.5L15.5 8" fill="none" stroke="#fff" stroke-width="1"/></svg>
          <span>info@lunellerosahair.example</span>
        </li>
        <li>
          <svg viewBox="0 0 22 22" aria-hidden="true"><circle cx="11" cy="11" r="9.5" fill="none" stroke="var(--brand-pink)" stroke-width="2"/><circle cx="11" cy="11" r="4.5" fill="none" stroke="var(--brand-pink)" stroke-width="1.4"/><path d="M6.5 11h9M11 6.5v9" stroke="var(--brand-pink)" stroke-width="1.2"/></svg>
          <span>www.lunellerosahair.example</span>
        </li>
      </ul>
    </div>
  </section>

  <section class="card card-back" aria-label="Business card back">
    <p class="brand-name">Lunelle Rosa Hair</p>
  </section>
</main>
</body>
</html>
```